Hair and Wellness Brochure and Pricelist design

I am requiring a brochure that has a fresh, though alternative design. My business name is The Quiet Orchard Hair and Wellness. I have a very professional approach to my work and love to give that little bit extra to all of my clients. My passion for health, has led me to channel my business alternatively by using non toxic colours and styling products and through that same vein, I have studied Aromatherapy, Indian Head Massage and Reiki...all additional services I use where required.
My studio has very neutral tones of beige,white and beech wood but these tones aren't necessarily required for the brochure.I like to create a space of calm, peace and quiet, where my clients feel refreshed and rejuvenated..

Industry/Entity Type

Business

```html
<!DOCTYPE html>
<html lang="en">
<head>
<meta charset="utf-8">
<title>The Quiet Orchard Hair and Wellness – Price List</title>
<link rel="stylesheet" href="https://fonts.googleapis.com/css2?family=Arimo:wght@400&display=swap">
<style>
  :root {
    --cream: #f4f2de;
    --cream-deep: #ebe7cf;
    --panel: #7b6b5a;
    --panel-edge: #6c5d4d;
    --panel-text: #f6f1e2;
    --wave-light: #cdc3b2;
    --wave-mid: #a99a88;
    --wave-dark: #7c6c5b;
    --brand-text: #f6f1e2;
  }
  * { margin: 0; padding: 0; box-sizing: border-box; }
  html, body { width: 1200px; height: 2770px; overflow: hidden; }
  body {
    background: var(--cream);
    font-family: "Arimo", Arial, sans-serif;
  }
  .pricelist {
    position: relative;
    width: 1200px;
    height: 2770px;
    background: linear-gradient(180deg, var(--cream) 0%, var(--cream-deep) 100%);
    overflow: hidden;
  }
  .service {
    position: absolute;
    left: 277px;
    width: 660px;
    background: var(--panel);
    border: 2px solid var(--panel-edge);
    border-radius: 14px;
    box-shadow: 0 4px 10px rgba(70, 55, 40, 0.25);
    color: var(--panel-text);
    font-size: 44px;
    line-height: 1.3;
    text-align: center;
    display: flex;
    flex-direction: column;
    justify-content: center;
    padding: 0 40px;
  }
  .service--massage { top: 36px; height: 343px; }
  .service--upstyle { top: 500px; height: 214px; }
  .service--wedding { top: 856px; height: 295px; }
  .service--consult { top: 1294px; height: 200px; }
  .footer-waves {
    position: absolute;
    left: 0;
    bottom: 0;
    width: 1200px;
    height: 560px;
  }
  .brand {
    position: absolute;
    left: 0;
    right: 0;
    bottom: 120px;
    text-align: center;
    color: var(--brand-text);
    font-size: 58px;
    line-height: 1.35;
    letter-spacing: 4px;
  }
</style>
</head>
<body>
<main class="pricelist">
  <section class="service service--massage">
    <p>Indian Head Massage with a Reiki and Aromatherapy Infusion</p>
    <p>45mins</p>
    <p>$50</p>
  </section>
  <section class="service service--upstyle">
    <p>Hair up styling including hot tools</p>
    <p>$50</p>
  </section>
  <section class="service service--wedding">
    <p>All wedding hairstyling starts from</p>
    <p>$60 (Price on consultation)</p>
  </section>
  <section class="service service--consult">
    <p>Wedding up style consultation</p>
    <p>$50</p>
  </section>

  <svg class="footer-waves" viewBox="0 0 1200 560" preserveAspectRatio="none" aria-hidden="true">
    <path d="M0 110 C 300 20, 800 0, 1200 90 L1200 560 L0 560 Z" fill="var(--wave-light)"/>
    <path d="M0 220 C 350 120, 800 110, 1200 200 L1200 560 L0 560 Z" fill="var(--wave-mid)"/>
    <path d="M0 300 C 400 230, 800 230, 1200 290 L1200 560 L0 560 Z" fill="var(--wave-dark)"/>
  </svg>

  <p class="brand">The Quiet Orchard<br>Hair and Wellness</p>
</main>
</body>
</html>
```